Business Card for Beach theme sports bar called MORVIN

I need a business card designed for our employees, front and back. This will be used by the employees of two business locations to hand out to customers. I've attached the previous business cards we used at one time for a Dantells (it is now Morvin). Looking for a fresh new card that is elegant but has character.

Target Market(s)

30-60, middle class

Contact Information for Business Card

We are a beach bar and sports bar. I am looking for an elegant business card with the front to have the MORVIN logo. Then on the back I need it to allow a space for employees to write their names and for them to write in their schedule. I have attached our old cards with our old name Dantells so you can pull everything we need on the cards. one thing is missing is we have another location at 2615 W Calder Ridge Rd with a number of 702-418-9053. Since we will use it for both locations it should allow the employee to circle or check mark the bar which they work at.

Font styles to use
Sans Serif

Requirements
Must have
• We are looking for some fresh ideas for the business card. Something that will really stick out to customers when the staff hands them out. Creativity will be looked at positively, but we still want it to look upscale and fun.

```html
<!DOCTYPE html>
<html lang="en">
<head>
<meta charset="utf-8">
<title>Morvin Business Card</title>
<link rel="stylesheet" href="https://fonts.googleapis.com/css2?family=Work+Sans:wght@400;500&display=swap">
<style>
  :root {
    --stage: #1c1c1c;
    --card-dark: #161616;
    --card-light: #ffffff;
    --ink: #1f1f1f;
    --ink-soft: #333333;
    --ink-faint: #8a8a8a;
    --silver: #b9b9b9;
    --band: #1a1a1a;
  }
  * { box-sizing: border-box; margin: 0; padding: 0; }
  html, body {
    width: 1200px; height: 900px; overflow: hidden;
    background: var(--stage);
    font-family: "Work Sans", sans-serif;
  }
  .stage { position: relative; width: 1200px; height: 900px; }
  .card {
    position: absolute; left: 290px; width: 620px; height: 354px;
    overflow: hidden;
  }
  .card--front { top: 70px; background: var(--card-dark); }
  .card--back { top: 476px; background: var(--card-light); color: var(--ink); }

  .brand { position: absolute; display: flex; align-items: center; gap: 12px; }
  .brand__dot { border-radius: 50%; border: 2px solid currentColor; }
  .brand__name { font-weight: 500; letter-spacing: 0.04em; }

  .card--front .brand {
    left: 50%; top: 50%; transform: translate(-50%, -50%);
    color: var(--silver);
  }
  .card--front .brand__dot { width: 22px; height: 22px; }
  .card--front .brand__name { font-size: 44px; }

  .card--back .brand { left: 40px; top: 46px; color: var(--ink); }
  .card--back .brand__dot { width: 20px; height: 20px; }
  .card--back .brand__name { font-size: 40px; }

  .write-in { position: absolute; left: 330px; top: 40px; width: 250px; }
  .write-in__field { display: flex; align-items: flex-end; gap: 10px; height: 34px; }
  .write-in__label {
    font-size: 10px; font-weight: 500; letter-spacing: 0.14em;
    color: var(--ink-soft); width: 70px; padding-bottom: 2px;
  }
  .write-in__line { flex: 1; border-bottom: 1px solid var(--ink-faint); height: 100%; }

  .rule { position: absolute; height: 1.5px; background: var(--ink); }
  .rule--top { left: 24px; right: 40px; top: 182px; }
  .rule--name { left: 300px; right: 40px; top: 262px; }

  .contact { position: absolute; left: 24px; top: 200px; list-style: none; font-size: 14px; color: var(--ink-soft); }
  .contact li { display: flex; align-items: center; gap: 8px; height: 23px; }
  .contact svg { width: 10px; height: 10px; fill: none; stroke: var(--ink-soft); stroke-width: 1.4; }

  .person { position: absolute; right: 40px; top: 200px; text-align: right; }
  .person__name { font-size: 19px; font-weight: 500; letter-spacing: 0.06em; }
  .person__role { font-size: 13px; margin-top: 5px; color: var(--ink-soft); }

  .locations { position: absolute; right: 40px; top: 272px; list-style: none; font-size: 12.5px; color: var(--ink-soft); }
  .locations li { display: flex; align-items: center; justify-content: flex-end; gap: 8px; height: 21px; }
  .locations__box { width: 10px; height: 10px; border: 1.2px solid var(--ink); }

  .band { position: absolute; left: 0; bottom: 0; width: 620px; height: 48px; }
</style>
</head>
<body>
<main class="stage">
  <section class="card card--front">
    <div class="brand">
      <span class="brand__dot"></span>
      <span class="brand__name">Morvin</span>
    </div>
  </section>

  <section class="card card--back">
    <div class="brand">
      <span class="brand__dot"></span>
      <span class="brand__name">Morvin</span>
    </div>

    <div class="write-in">
      <div class="write-in__field"><span class="write-in__label">NAME</span><span class="write-in__line"></span></div>
      <div class="write-in__field"><span class="write-in__label">SCHEDULE</span><span class="write-in__line"></span></div>
      <div class="write-in__field"><span class="write-in__label"></span><span class="write-in__line"></span></div>
    </div>

    <div class="rule rule--top"></div>

    <ul class="contact">
      <li><svg viewBox="0 0 10 10"><path d="M2 1 L4 1 L5 3.5 L3.8 4.5 Q5 6.5 6 7 L7 5.8 L9 7 L9 9 Q4 9 1 3 Z"/></svg>(514) 603-7718</li>
      <li><svg viewBox="0 0 10 10"><rect x="1" y="2" width="8" height="6"/><path d="M1 2 L5 5.5 L9 2"/></svg>info@morvin.com</li>
      <li><svg viewBox="0 0 10 10"><circle cx="5" cy="5" r="4"/><path d="M1 5 H9 M5 1 Q2.5 5 5 9 M5 1 Q7.5 5 5 9"/></svg>www.morvin.com</li>
    </ul>

    <div class="person">
      <p class="person__name">DANIEL HART</p>
      <p class="person__role">Director</p>
    </div>

    <div class="rule rule--name"></div>

    <ul class="locations">
      <li>418b Harlow Street, Wellmont, NZ, 8042<span class="locations__box"></span></li>
      <li>2615 W Calder Ridge Rd · 702-418-9053<span class="locations__box"></span></li>
    </ul>

    <svg class="band" viewBox="0 0 620 48" aria-hidden="true">
      <path d="M0 0 L270 0 Q290 0 300 10 Q310 20 330 20 L620 20 L620 48 L0 48 Z" fill="var(--band)"/>
      <path d="M0 7 L268 7 Q282 7 290 12" stroke="var(--card-light)" stroke-width="2.5" fill="none"/>
    </svg>
  </section>
</main>
</body>
</html>
```